Venture Capital Firm Needs Website Redesign

We need a bold revamp of our website (https://halverine.vc/)
which at the moment looks washed out. We want a crisp, fresh and unique look. Feel free to keep as much or as little content in the site. The only thing we need to keep is a team section. The site should convey a clear distinction between our 3 product lines: Venture Capital, Private Credit, and Crypto. Two versions of our logo are attached and they should not change. For design inspirations, we like http://www.9plm.com/ for a more simple site and for a more built out site we like http://bluetorch.com/

Updates
Industry/Entity Type
Investment
Coding
Coded - Design and coding required
Number of Pages Required
1 page
Font styles to use
Colors
Designer to choose colors to be used in the design.
Requirements
Must have
- - Clear distinction between our 3 product lines: Venture Capital, Private Credit
- - Team section

Nice to have
- Some really creative aspect like http://www.9plm.com/ has with the distinction between first, second, and third kind

```html
<!DOCTYPE html>
<html lang="en">
<head>
<meta charset="utf-8">
<title>Halverine</title>
<link rel="stylesheet" href="https://fonts.googleapis.com/css2?family=Exo+2:wght@500;600&family=Tenor+Sans&family=Arimo:wght@400;700&display=swap">
<style>
:root{
  --green:#7f9a5d;
  --green-light:#8ea56f;
  --ink:#2a2a2a;
  --body:#3a3a3a;
  --page:#f2f3f5;
  --white:#ffffff;
  --hero-deep:#0b2d45;
  --hero-mid:#1d6390;
  --hero-light:#9ec9e3;
}
*{box-sizing:border-box;margin:0;padding:0}
html,body{width:738px;height:1200px;overflow:hidden}
body{position:relative;background:var(--page);font-family:"Arimo",Arial,sans-serif;color:var(--body)}

.hero{position:absolute;left:0;top:0;width:738px;height:370px;
  background:radial-gradient(ellipse 260px 220px at 600px 190px,var(--hero-light) 0%,#4f97c3 35%,transparent 75%),
  linear-gradient(180deg,var(--hero-mid) 0%,#134a6e 50%,var(--hero-deep) 100%)}
.brand{position:absolute;left:62px;top:10px;width:60px;text-align:center;color:var(--white);font-family:"Exo 2",sans-serif}
.brand-ring{width:36px;height:36px;border:1.5px solid var(--white);border-radius:50%;margin:0 auto 4px}
.brand-name{font-size:9px;letter-spacing:.6px;text-transform:uppercase}
.nav{position:absolute;right:62px;top:25px;display:flex;gap:12px;font-family:"Exo 2",sans-serif;font-size:11.5px;font-weight:500;color:var(--white)}
.nav a{color:inherit;text-decoration:none}
.nav .current{border-bottom:1px solid var(--white);padding-bottom:2px}
.hero-title{position:absolute;left:62px;top:122px;width:320px;font-family:"Tenor Sans",sans-serif;font-weight:400;font-size:21.5px;line-height:27px;color:var(--white)}
.btn{display:inline-block;background:var(--green-light);color:var(--white);font-family:"Arimo",sans-serif;font-size:9.5px;padding:4px 13px;border-radius:10px}
.hero .btn{position:absolute;left:62px;top:207px}

.lines{position:absolute;left:69px;top:333px;width:601px;height:175px;background:var(--white);
  box-shadow:0 2px 4px rgba(0,0,0,.35);display:flex}
.line{flex:1;text-align:center;padding-top:13px;border-right:1px solid #e3e3e3;margin:18px 0 20px}
.line:last-child{border-right:none}
.line{padding-top:0;margin-top:0}
.line svg{display:block;margin:13px auto 0}
.line h3{font-family:"Exo 2",sans-serif;font-weight:500;font-size:13.5px;color:var(--ink);margin:6px 0 9px}
.line p{font-size:7.2px;line-height:12px;width:130px;margin:0 auto;color:var(--body)}

.about{position:absolute;left:70px;top:552px;width:598px;text-align:center}
.about h2{font-family:"Exo 2",sans-serif;font-weight:600;font-size:21px;color:var(--ink);margin-bottom:12px}
.about p{font-size:9.2px;line-height:17.2px}

.team{position:absolute;left:0;top:698px;width:738px;height:306px;text-align:center;color:var(--white)}
.team-photo{position:absolute;inset:0;background:linear-gradient(90deg,#4a4a4a,#5a5a5a 30%,#3f3f3f 60%,#555 100%)}
.team-inner{position:relative;padding-top:90px}
.team h2{font-family:"Exo 2",sans-serif;font-weight:500;font-size:20px;margin-bottom:9px}
.team .lead{font-family:"Exo 2",sans-serif;font-weight:500;font-size:14.5px;line-height:22px;width:540px;margin:0 auto}
.values{display:flex;justify-content:center;gap:24px;font-family:"Arimo",sans-serif;font-size:14px;margin-top:9px}
.team .btn{margin-top:11px;padding:4px 10px}

.contact{position:absolute;left:0;top:1004px;width:738px;height:172px;background:var(--white)}
.mark{position:absolute;left:196px;top:30px;width:124px;height:124px;border:2.5px solid var(--ink);border-radius:50%;
  display:flex;align-items:center;justify-content:center;font-family:"Exo 2",sans-serif;font-weight:500;font-size:17px;color:var(--ink)}
.details{position:absolute;left:340px;top:50px;list-style:none;font-family:"Exo 2",sans-serif;font-weight:500;font-size:13px;color:var(--ink)}
.details li{display:flex;align-items:flex-start;gap:14px;margin-bottom:10px;line-height:15px}
.details svg{flex:none;margin-top:1px}

.copyright{position:absolute;left:0;top:1176px;width:738px;height:24px;background:var(--green-light);
  font-size:7.5px;color:#3a3a3a;text-align:center;line-height:24px}
</style>
</head>
<body>

<header class="hero">
  <div class="hero-photo" role="img" aria-label="Close-up photograph of glowing blue fibre optic strands"></div>
  <div class="brand"><div class="brand-ring"></div><div class="brand-name">Halverine</div></div>
  <nav class="nav">
    <a class="current" href="#">Home</a><a href="#">Venture Capital</a><a href="#">Private Credit</a><a href="#">Crypto</a><a href="#">Team</a><a href="#">Blog</a><a href="#">Contact Us</a>
  </nav>
  <h1 class="hero-title">Halverine Operates At The Intersection Of Technology And Novel Asset Classes.</h1>
  <span class="btn">Learn More</span>
</header>

<section class="lines">
  <article class="line">
    <svg width="54" height="54" viewBox="0 0 54 54" fill="none" stroke="#7f9a5d" stroke-width="1.6">
      <circle cx="28" cy="16" r="13"/><circle cx="28" cy="16" r="9"/>
      <path d="M28 10v12M31 12.5c-1-1.5-6-1.5-6 1s6 1.5 6 4-5 2.5-6 1"/>
      <rect x="4" y="36" width="6" height="14"/><path d="M10 39h12l6 3h8l12-6c3-1 4 2 2 3l-14 9H10"/>
    </svg>
    <h3>Venture Capital</h3>
    <p>We invest in early-stage startups led by founders who are passionate and knowledgeable about the....[+]</p>
  </article>
  <article class="line">
    <svg width="66" height="54" viewBox="0 0 66 54" fill="none" stroke="#7f9a5d" stroke-width="1.8">
      <rect x="3" y="12" width="50" height="34" rx="3"/><path d="M12 5h46a3 3 0 0 1 3 3v26"/>
      <circle cx="16" cy="29" r="5"/><circle cx="24" cy="29" r="5"/><circle cx="44" cy="25" r="5"/><path d="M44 30v8"/>
    </svg>
    <h3>Private Credit</h3>
    <p>Halverine Private Credit provides capital to lending businesses that are focused on using technology...[+]t.</p>
  </article>
  <article class="line">
    <svg width="62" height="54" viewBox="0 0 62 54" fill="none" stroke="#7f9a5d" stroke-width="1.6">
      <circle cx="30" cy="28" r="14"/><circle cx="30" cy="28" r="9"/>
      <path d="M3 50l8-10 6 4 7-9M40 16l9-9 5 4 6-8M54 3h6v6"/><path d="M45 16v-6M49 16v-9M53 16v-5"/>
    </svg>
    <h3>Crypto</h3>
    <p>The Halverine Crypto Index tracks the top 15 cryptocurrencies weighted by market cap and rebalanced...[+]</p>
  </article>
</section>

<section class="about">
  <h2>About Us</h2>
  <p>Halverine operates three businesses that bridge technology and finance. We invest in pre-seed venture capital, and build software for the companies we invest in. We manage direct private credit funds that provide private credit capital to alternative private credit platforms, enabling them to finance the loans they originate. We create crypto funds for individuals, IRAs and institutions to get simple and easy access to cryptocurrencies.</p>
</section>

<section class="team">
  <div class="team-photo" role="img" aria-label="Black and white grid of expressive team member portraits"></div>
  <div class="team-inner">
    <h2>Our Team</h2>
    <p class="lead">Our Highly Skilled Financial Consultants Are People Who Personifies The Very Qualities That Have Made Us Successful</p>
    <div class="values"><span>KNOWLEDGE.</span><span>EXPERIENCE.</span><span>ENTHUSIAM.</span><span>DEDICATION</span></div>
    <span class="btn">Read More</span>
  </div>
</section>

<footer class="contact">
  <div class="mark">Halverine</div>
  <ul class="details">
    <li><svg width="18" height="20" viewBox="0 0 18 20" fill="none" stroke="#7f9a5d" stroke-width="1.4"><path d="M9 16s5-5 5-9a5 5 0 0 0-10 0c0 4 5 9 5 9z"/><circle cx="9" cy="7" r="2"/><path d="M3 15l-2 4h16l-2-4"/></svg><span>218 Larkmoor Avenue, Suite 410<br>Brookvale, NY 10871</span></li>
    <li><svg width="18" height="14" viewBox="0 0 18 14" fill="#7f9a5d"><path d="M1 2h16v11H1z"/><path d="M1 2l8 6 8-6" stroke="#fff" stroke-width="1.2" fill="none"/></svg><span>info@halverine.vc</span></li>
    <li><svg width="18" height="18" viewBox="0 0 18 18" fill="none" stroke="#7f9a5d" stroke-width="1.4"><circle cx="9" cy="9" r="8"/><path d="M6 5c-1 3 1 7 5 8l1-2-2-1-1 1c-1-1-2-2-2-3l1-1-1-2z" fill="#7f9a5d"/></svg><span>555.014.2290</span></li>
  </ul>
</footer>

<div class="copyright">Copyright © 2018 Halverine &nbsp; All Rights Reserved</div>

</body>
</html>
```